Road Construction Company needs business cards

We would like a new business card designed for our business.

We're a road construction company based in Qld, Australia.

Can the business card please have the following information on it.

Name: Warren Halbeck
Position: General Manager
Phone: 0472 915 348
Email: Warren.halbeck@tovrin.com.au
Address: 87 Marrow Ave, Pendlebay, QLD, 4023
Website: www.tovrin.com.au

Visually we'd like the card to be professional and simple.

Attached is our logo.

Our website is www.tovrin.com.au

Target Market(s)

Men aged 25-60

Contact Information for Business Card

As listed in project description

Font styles to use
Serif

Requirements
Must have
• Large logo on back of card

```html
<!DOCTYPE html>
<html lang="en">
<head>
<meta charset="utf-8">
<title>Tovrin – Business Cards</title>
<link href="https://fonts.googleapis.com/css2?family=Montserrat:wght@400;500;700;800&display=swap" rel="stylesheet">
<style>
  :root {
    --brand-blue: #0d55a5;
    --sky-blue: #35a7dc;
    --paper: #ffffff;
    --backdrop-top: #cfcfcf;
    --backdrop-bottom: #a9a9a9;
  }
  * { margin: 0; padding: 0; box-sizing: border-box; }
  html, body { width: 1200px; height: 815px; overflow: hidden; }
  body {
    background: linear-gradient(180deg, var(--backdrop-top), var(--backdrop-bottom));
    font-family: "Montserrat", Arial, sans-serif;
    position: relative;
  }
  .card {
    position: absolute;
    top: 252px;
    width: 540px;
    height: 310px;
    border-radius: 24px;
    overflow: hidden;
    box-shadow: 0 14px 30px rgba(0, 0, 0, 0.28);
  }
  .card--front { left: 40px; background: var(--paper); }
  .card--back { left: 620px; background: var(--brand-blue); }

  .front-wave { position: absolute; inset: 0; }

  .wordmark {
    position: absolute;
    font-weight: 800;
    letter-spacing: 2px;
    line-height: 1;
  }
  .card--front .wordmark {
    left: 64px; top: 46px;
    font-size: 54px;
    color: var(--brand-blue);
  }
  .card--back .wordmark {
    left: 0; right: 0; top: 104px;
    text-align: center;
    font-size: 104px;
    color: var(--paper);
  }

  .address {
    position: absolute;
    right: 24px; bottom: 22px;
    text-align: right;
    color: var(--paper);
    font-size: 13px;
    line-height: 1.45;
  }

  .contact-block {
    position: absolute;
    left: 34px; top: 182px;
    color: var(--paper);
  }
  .contact-name {
    font-size: 24px;
    font-weight: 700;
    color: var(--sky-blue);
    line-height: 1.1;
  }
  .contact-role {
    font-size: 14px;
    font-weight: 500;
    margin-bottom: 7px;
  }
  .contact-line {
    display: flex;
    align-items: center;
    gap: 8px;
    font-size: 13px;
    line-height: 19px;
  }
  .contact-icon { width: 12px; height: 12px; flex: none; }
</style>
</head>
<body>

  <section class="card card--front" aria-label="Business card front">
    <svg class="front-wave" viewBox="0 0 540 310" width="540" height="310" aria-hidden="true">
      <path d="M0 174 C 30 140 80 126 160 122 C 300 116 400 95 416 0 L 440 0 C 420 110 300 134 160 138 C 80 140 30 150 0 180 Z" fill="var(--sky-blue)"/>
      <path d="M0 186 C 30 156 80 146 160 144 C 305 140 428 114 448 0 L 540 0 L 540 310 L 0 310 Z" fill="var(--brand-blue)"/>
    </svg>

    <div class="wordmark">TOVRIN</div>

    <p class="address">87 Marrow Ave,<br>Pendlebay, QLD, 4023</p>

    <div class="contact-block">
      <p class="contact-name">Warren Halbeck</p>
      <p class="contact-role">General Manager</p>
      <p class="contact-line">
        <svg class="contact-icon" viewBox="0 0 12 12" aria-hidden="true"><path d="M2.5 1 L4.5 1 L5.3 3.6 L4 4.6 C4.6 6 5.8 7.3 7.3 8 L8.4 6.7 L11 7.5 L11 9.5 C11 10.3 10.3 11 9.5 11 C5 11 1 7 1 2.5 C1 1.7 1.7 1 2.5 1 Z" fill="var(--sky-blue)"/></svg>
        0472 915 348
      </p>
      <p class="contact-line">
        <svg class="contact-icon" viewBox="0 0 12 12" aria-hidden="true"><rect x="0.5" y="2" width="11" height="8" rx="1" fill="var(--sky-blue)"/><path d="M1 2.5 L6 6.5 L11 2.5" fill="none" stroke="var(--brand-blue)" stroke-width="1"/></svg>
        Warren.halbeck@tovrin.com.au
      </p>
      <p class="contact-line">
        <svg class="contact-icon" viewBox="0 0 12 12" aria-hidden="true"><circle cx="6" cy="6" r="5.3" fill="none" stroke="var(--sky-blue)" stroke-width="1.2"/><ellipse cx="6" cy="6" rx="2.2" ry="5.3" fill="none" stroke="var(--sky-blue)" stroke-width="1"/><path d="M0.8 6 H11.2" stroke="var(--sky-blue)" stroke-width="1"/></svg>
        www.tovrin.com.au
      </p>
    </div>
  </section>

  <section class="card card--back" aria-label="Business card back">
    <div class="wordmark">TOVRIN</div>
  </section>

</body>
</html>
```